Concierge Dental / Medical Supply Ordering Business - Sleek, Efficient, Professional, Elite

www.brantonkeelmedical.com - example website.

We are a concierge supply ordering business for medical and dental that provide DSO price savings on supplies while maintaining business autonomy and independence.

We want a very simple website that looks very professional says what we do and gives a very simple method to contact us & sign up as above.

Target Market(s)

Independent Dental and Medical Practices

Industry/Entity Type

Dental and Medical - healthcare

Coding

Coded - Design and coding required

Number of Pages Required

3 page

Font styles to use
Sans Serif

Colors
0054AA
0677BA
7BADD7
CADEEF
E8F1F8

Requirements
Must have
• Simple contact page, sleek efficient design, uncomplicated.
Nice to have
• Sign up page vs just a contact page.
Should not have
• Lots of pages, hard to navigate,

```html
<!DOCTYPE html>
<html lang="en">
<head>
<meta charset="utf-8">
<title>Keelridge Dental Supply</title>
<link href="https://fonts.googleapis.com/css2?family=Open+Sans:wght@400;600;700;800&display=swap" rel="stylesheet">
<style>
:root{
  --navy:#0f2c72;
  --deep:#0b2340;
  --primary:#0054AA;
  --accent:#0677BA;
  --sky:#7BADD7;
  --mist:#CADEEF;
  --ice:#E8F1F8;
  --ink:#3d4650;
  --muted:#6b7480;
  --white:#ffffff;
}
*{margin:0;padding:0;box-sizing:border-box}
html,body{width:1200px;height:3824px;overflow:hidden}
body{position:relative;font-family:"Open Sans",Arial,sans-serif;color:var(--ink);background:var(--white)}
.abs{position:absolute}
a{text-decoration:none;color:inherit}

/* header */
.site-header{left:0;top:0;width:1200px;height:64px;background:rgba(255,255,255,.96);z-index:5}
.brand-mark{left:178px;top:20px;display:flex;align-items:center;gap:8px;font-weight:700;font-size:13px;color:var(--navy)}
.brand-mark .sq{width:22px;height:22px;background:var(--primary);border-radius:4px}
.main-nav{left:352px;top:0;height:64px;display:flex;gap:54px;align-items:center;font-size:13px;font-weight:700;color:var(--navy);letter-spacing:.5px}
.quote-btn{left:890px;top:0;width:310px;height:64px;background:var(--navy);color:var(--white);font-size:13px;font-weight:700;display:flex;align-items:center;padding-left:44px;gap:18px;letter-spacing:.5px}

/* hero */
.hero{left:0;top:0;width:1200px;height:640px;background:linear-gradient(120deg,#c9d3dc 0%,#e6ebef 35%,#aab6c2 65%,#7c8b99 100%)}
.hero-panel{left:92px;top:228px;width:580px;height:270px;background:rgba(20,32,48,.72);padding:34px 40px}
.hero-panel h1{font-size:36px;line-height:44px;font-weight:700;color:var(--white)}
.hero-panel p{margin-top:14px;font-size:14px;line-height:21px;color:#dfe6ee;width:470px}
.btn{display:inline-block;background:var(--accent);color:var(--white);font-size:13px;font-weight:700;letter-spacing:.5px;padding:11px 26px;border-radius:3px}
.hero-panel .btn{margin-top:22px}

/* features */
.features{left:180px;top:722px;width:880px;display:flex;justify-content:space-between}
.feature{display:flex;gap:14px;width:270px}
.feature .ico{flex:none;width:50px;height:50px;border-radius:50%;background:var(--primary);display:flex;align-items:center;justify-content:center}
.feature h3{font-size:15px;font-weight:700;color:var(--navy);margin-top:2px}
.feature p{font-size:12px;line-height:17px;color:var(--muted);margin-top:4px}

/* about */
.about-band{left:280px;top:860px;width:920px;height:440px;background:linear-gradient(90deg,var(--white) 0%,var(--ice) 40%,#dfe7ee 100%);clip-path:polygon(0 0,100% 0,100% 100%,8% 100%)}
.about-photo{left:122px;top:876px;width:370px;height:400px;background:linear-gradient(135deg,#d8e2ea,#8fa3b4 60%,#4f6478);border-bottom:6px solid var(--accent)}
.about-text{left:562px;top:946px;width:620px}
.eyebrow{font-size:11px;font-weight:700;letter-spacing:1.5px;color:var(--accent)}
.about-text h2{font-size:31px;font-weight:700;color:var(--navy);margin:8px 0 14px;white-space:nowrap}
.about-text h2 span{color:var(--accent)}
.about-text p{font-size:13.5px;line-height:20px;color:var(--ink);margin-bottom:10px}

/* section titles */
.sec-head{left:0;width:1200px;text-align:center}
.sec-head .eyebrow{display:flex;justify-content:center;align-items:center;gap:12px}
.sec-head .eyebrow::before,.sec-head .eyebrow::after{content:"";width:60px;height:1px;background:var(--sky)}
.sec-head h2{margin-top:10px;font-size:46px;font-weight:700;color:var(--navy)}

/* services */
.services{left:122px;top:1572px;width:956px;display:flex;gap:26px}
.service-card{width:300px;height:262px;background:var(--white);box-shadow:0 4px 18px rgba(15,44,114,.12);border-radius:4px;overflow:hidden}
.service-card .ph{height:140px;background:linear-gradient(135deg,#cfd9e2,#7f93a6)}
.service-card h3{display:flex;align-items:center;gap:8px;font-size:17px;font-weight:700;color:var(--navy);padding:16px 18px 6px}
.service-card p{font-size:12.5px;line-height:18px;color:var(--muted);padding:0 18px}

/* banner */
.banner{left:0;top:1950px;width:1200px;height:310px}
.banner-text{left:300px;top:2040px;width:600px;text-align:center;color:var(--white)}
.banner-text h2{font-size:34px;line-height:42px;font-weight:800;letter-spacing:.5px}
.banner-text p{font-size:15px;margin-top:8px;color:#e3ecf4}
.banner-text .btn{margin-top:16px;border-radius:22px;padding:10px 26px}

/* reviews */
.reviews{left:92px;top:2530px;width:1016px;display:flex;gap:28px;align-items:flex-start}
.review{width:320px;height:176px;margin-top:12px;background:#f5f7f9;box-shadow:0 3px 14px rgba(0,0,0,.08);padding:30px 32px;text-align:center;font-size:13px;line-height:19px;color:var(--muted);position:relative}
.review.featured{height:196px;margin-top:0;background:var(--navy);color:var(--white);padding-top:46px}
.review::after{content:"";position:absolute;left:50%;bottom:-12px;margin-left:-12px;border:12px solid transparent;border-bottom:0;border-top-color:#f5f7f9}
.review.featured::after{border-top-color:var(--navy)}
.reviewers{left:92px;top:2762px;width:1016px;display:flex;gap:28px}
.reviewer{width:320px;text-align:center}
.reviewer .av{width:44px;height:44px;border-radius:50%;background:linear-gradient(135deg,#9aa8b5,#5b6a79);margin:0 auto 6px}
.reviewer b{display:block;font-size:11px;color:var(--ink)}
.reviewer span{font-size:10px;color:var(--muted)}

/* contact */
.contact-bg{left:0;top:2880px;width:1200px;height:460px;background:var(--ice);border-top:1px solid var(--mist)}
.contact-cards{left:130px;top:3068px;width:940px;display:flex;gap:30px}
.contact-card{width:293px;height:178px;background:var(--white);box-shadow:0 3px 14px rgba(15,44,114,.08);text-align:center;padding-top:18px}
.contact-card svg{display:block;margin:0 auto 8px}
.contact-card h4{font-size:13px;font-weight:700;color:var(--ink);letter-spacing:.5px}
.contact-card p{font-size:12px;line-height:17px;color:var(--muted)}
.contact-card .more{display:inline-block;margin-top:10px;font-size:11px;font-weight:700;color:var(--accent);border-bottom:1px solid var(--accent);padding-bottom:3px}

/* footer */
.footer{left:0;top:3280px;width:1200px;height:544px}
.footer-col{color:var(--white)}
.footer-col h5{font-size:15px;font-weight:700;margin-bottom:20px;letter-spacing:.5px}
.footer-list li{list-style:none;display:flex;gap:12px;font-size:12px;line-height:17px;color:#c6d2de;margin-bottom:18px}
.footer-list .dot{flex:none;width:12px;height:12px;border-radius:50%;background:var(--sky);margin-top:2px}
.footer-brand{left:400px;top:3480px;width:400px;text-align:center;color:var(--white)}
.footer-brand .sq{display:block;width:40px;height:40px;border-radius:6px;background:var(--accent);margin:0 auto 10px}
.footer-brand .name{font-weight:700;font-size:16px}
.footer-brand p{font-size:12px;line-height:18px;color:#c6d2de;margin-top:12px}
.socials{display:flex;justify-content:center;gap:12px;margin-top:18px}
.socials span{width:28px;height:28px;border:1px solid #5f7893;border-radius:3px}
.hours li{list-style:none;font-size:12px;color:#c6d2de;margin-bottom:10px}
.hours b{color:var(--white);border-bottom:1px solid var(--white)}
.footer-bottom{left:0;top:3770px;width:1200px;border-top:1px solid #2a4563;text-align:center;font-size:12px;color:#c6d2de;padding-top:18px}
</style>
</head>
<body>

<section class="hero abs" role="img" aria-label="Photo of medical professionals working together at a desk with laptops"></section>

<header class="site-header abs">
  <div class="brand-mark abs"><span class="sq"></span>Keelridge</div>
  <nav class="main-nav abs"><a>HOME</a><a>ABOUT US</a><a>SERVICES</a><a>CONTACT US</a></nav>
  <a class="quote-btn abs"><svg width="12" height="12" viewBox="0 0 12 12"><path d="M3 1l5 5-5 5" stroke="#fff" stroke-width="2" fill="none"/></svg>GET QUOTATION</a>
</header>

<div class="hero-panel abs">
  <h1>Your Gateway To Efficient Medical Supply Ordering</h1>
  <p>We handle supply ordering for independent practices so you keep group-level savings and full control of your business.</p>
  <a class="btn">REQUEST A DEMO</a>
</div>

<section class="features abs">
  <div class="feature"><div class="ico"><svg width="24" height="24" viewBox="0 0 24 24" fill="none" stroke="#fff" stroke-width="1.8"><circle cx="12" cy="12" r="9"/><path d="M3 12h18M12 3c3 3 3 15 0 18M12 3c-3 3-3 15 0 18"/></svg></div>
    <div><h3>Global Reach</h3><p>Trusted suppliers across many regions, sourced for value and reliable delivery.</p></div></div>
  <div class="feature"><div class="ico"><svg width="24" height="24" viewBox="0 0 24 24" fill="none" stroke="#fff" stroke-width="1.8"><circle cx="12" cy="8" r="4"/><path d="M4 21c1-5 15-5 16 0"/></svg></div>
    <div><h3>Client Centric</h3><p>Your practice comes first with personal service and a dedicated account team.</p></div></div>
  <div class="feature"><div class="ico"><svg width="24" height="24" viewBox="0 0 24 24" fill="none" stroke="#fff" stroke-width="1.8"><path d="M12 3l2.7 5.6 6 .8-4.4 4.2 1 6-5.3-2.9-5.3 2.9 1-6L3.3 9.4l6-.8z"/></svg></div>
    <div><h3>Professionalism and Expertise</h3><p>Years of supply know-how applied to every order we place.</p></div></div>
</section>

<div class="about-band abs"></div>
<div class="about-photo abs" role="img" aria-label="Photo of two doctors reviewing a tablet in a clinic"></div>
<section class="about-text abs">
  <div class="eyebrow">ABOUT US</div>
  <h2>Welcome To <span>Keelridge Dental Supply</span></h2>
  <p>We are a concierge ordering service for dental and medical practices. We bring you the buying power of large groups while you stay fully independent and in charge of every choice you make for your team and patients.</p>
  <p>Our specialists compare prices, manage orders and track deliveries, so your staff spend less time on paperwork and more time on care.</p>
  <p>From gloves to major equipment, we find the right product at the right price and keep your shelves stocked without any long contracts.</p>
</section>

<div class="sec-head abs" style="top:1436px">
  <div class="eyebrow">SERVICES</div>
  <h2>Services We Provide</h2>
</div>
<section class="services abs">
  <article class="service-card"><div class="ph" role="img" aria-label="Photo of a team discussing supply orders"></div>
    <h3><svg width="18" height="18" viewBox="0 0 18 18" fill="none" stroke="#0f2c72" stroke-width="1.8"><circle cx="9" cy="9" r="7.5"/><path d="M5.5 9l2.5 2.5 4.5-5"/></svg>Order Fulfillment</h3>
    <p>We place, confirm and follow each order from quote to your front door.</p></article>
  <article class="service-card"><div class="ph" role="img" aria-label="Photo of colleagues reviewing pricing"></div>
    <h3><svg width="18" height="18" viewBox="0 0 18 18" fill="none" stroke="#0f2c72" stroke-width="1.8"><path d="M2 9V2h7l7 7-7 7z"/><circle cx="5.5" cy="5.5" r="1.2"/></svg>Price Savings</h3>
    <p>Group-level pricing on supplies while you keep your practice independent.</p></article>
  <article class="service-card"><div class="ph" role="img" aria-label="Photo of staff checking a delivery schedule"></div>
    <h3><svg width="18" height="18" viewBox="0 0 18 18" fill="none" stroke="#0f2c72" stroke-width="1.8"><circle cx="9" cy="9" r="7.5"/><path d="M9 4.5V9l3 2"/></svg>Timely Delivery</h3>
    <p>Reliable shipping schedules so you never run short of what you need.</p></article>
</section>

<svg class="banner abs" width="1200" height="310" viewBox="0 0 1200 310" role="img" aria-label="Dark photo of professionals in a meeting">
  <defs><linearGradient id="bannerFill" x1="0" y1="0" x2="1" y2="1"><stop offset="0" stop-color="#27323d"/><stop offset=".5" stop-color="#3d4a57"/><stop offset="1" stop-color="#1c252e"/></linearGradient></defs>
  <path d="M0 40 Q600 -20 1200 40 L1200 270 Q600 330 0 270 Z" fill="url(#bannerFill)"/>
</svg>
<div class="banner-text abs">
  <h2>PROVIDING EXPERT SUPPLY ORDERING SERVICES</h2>
  <p>Get in touch with us for the best experienced professional services</p>
  <a class="btn">CONTACT US &rarr;</a>
</div>

<div class="sec-head abs" style="top:2420px">
  <div class="eyebrow">TESTIMONIALS</div>
  <h2>Client Reviews</h2>
</div>
<section class="reviews abs">
  <div class="review">Keelridge cut our supply spend noticeably and the ordering now runs smoothly without any effort from our front desk team.</div>
  <div class="review featured">We kept our independence and still pay group prices. Their team is fast, friendly and always on top of our orders.</div>
  <div class="review">Deliveries arrive on time and the savings report each month shows exactly where our money goes. Highly recommended.</div>
</section>
<section class="reviewers abs">
  <div class="reviewer"><div class="av" role="img" aria-label="Client portrait"></div><b>Ryan Hale</b><span>Practice Owner</span></div>
  <div class="reviewer"><div class="av" role="img" aria-label="Client portrait"></div><b>Nora Pike</b><span>Office Manager</span></div>
  <div class="reviewer"><div class="av" role="img" aria-label="Client portrait"></div><b>Owen Marsh</b><span>Dentist</span></div>
</section>

<div class="contact-bg abs"></div>
<div class="sec-head abs" style="top:2934px">
  <div class="eyebrow">CONTACT US</div>
  <h2>Get in touch with us</h2>
</div>
<section class="contact-cards abs">
  <div class="contact-card"><svg width="30" height="30" viewBox="0 0 30 30" fill="none" stroke="#0677BA" stroke-width="1.8"><path d="M15 27s9-8 9-15a9 9 0 0 0-18 0c0 7 9 15 9 15z"/><circle cx="15" cy="12" r="3"/></svg>
    <h4>FIND US</h4><p>120 Harbor Lane<br>Suite 4, Springfield</p><a class="more">CONTACT US &rarr;</a></div>
  <div class="contact-card"><svg width="30" height="30" viewBox="0 0 30 30" fill="none" stroke="#0677BA" stroke-width="1.8"><path d="M7 4h5l2 6-3 2a14 14 0 0 0 7 7l2-3 6 2v5a2 2 0 0 1-2 2C13 25 5 17 5 6a2 2 0 0 1 2-2z"/></svg>
    <h4>CALL US AT</h4><p>+1 555 010 4477<br>hello@keelridgesupply.com</p><a class="more">CONTACT US &rarr;</a></div>
  <div class="contact-card"><svg width="30" height="30" viewBox="0 0 30 30" fill="none" stroke="#0677BA" stroke-width="1.8"><rect x="4" y="7" width="22" height="16" rx="2"/><path d="M4 9l11 8 11-8"/></svg>
    <h4>EMAIL US</h4><p>+1 555 010 4477<br>hello@keelridgesupply.com</p><a class="more">CONTACT US &rarr;</a></div>
</section>

<svg class="footer abs" width="1200" height="544" viewBox="0 0 1200 544" aria-hidden="true">
  <path d="M0 30 Q300 0 600 20 T1200 10 L1200 544 L0 544 Z" fill="#0b2340"/>
  <path d="M0 30 Q300 0 600 20 T1200 10" stroke="#7BADD7" stroke-width="3" fill="none"/>
</svg>

<div class="footer-col abs" style="left:92px;top:3508px">
  <h5>CONTACT US</h5>
  <ul class="footer-list">
    <li><span class="dot"></span>120 Harbor Lane, Suite 4<br>Springfield, United States</li>
    <li><span class="dot"></span>+1 555 010 4477</li>
    <li><span class="dot"></span>hello@keelridgesupply.com</li>
  </ul>
</div>
<div class="footer-brand abs">
  <span class="sq"></span>
  <div class="name">Keelridge Dental Supply</div>
  <p>Concierge supply ordering for independent dental and medical practices. Group savings, full autonomy, one simple partner.</p>
  <div class="socials"><span></span><span></span><span></span></div>
</div>
<div class="footer-col abs" style="left:930px;top:3508px">
  <h5>OPENING HOURS</h5>
  <ul class="hours">
    <li>Mon - Fri: 9am - 6pm</li>
    <li>Saturday: 9am - 2pm</li>
    <li>Sunday: <b>Closed</b></li>
  </ul>
</div>
<div class="footer-bottom abs">Keelridge Dental Supply</div>

</body>
</html>
```